Tolvik Commercial Cleaning is lookong for a new business card design.

A fresh new design that's professional and stylish. We need a serious upgrade to our business cards. I have included pictures of our existing ones. Our clients include professional individuals and business owners. We woupdblike something professional and upbeat. Please have fun and see what you come uo with.

Target Market(s)

Property managers, business owners, facility managers and other similar professionals

Industry/Entity Type

Janitorial

Contact Information for Business Card

Name, cell, office number, email, web address

Font styles to use
Sans Serif

Colors

Designer to choose colors to be used in the design.

Requirements
Must have
• please use the green color in our logo
Nice to have
• Bar code
Should not have
• Address

```html
<!DOCTYPE html>
<html lang="en">
<head>
<meta charset="utf-8">
<title>Tolvik Commercial Cleaning – Business Card</title>
<link rel="stylesheet" href="https://fonts.googleapis.com/css2?family=Comfortaa:wght@300;700&family=Open+Sans:wght@400&display=swap">
<style>
  :root {
    --backdrop: #d3d4d6;
    --brand-green: #4aae58;
    --brand-green-light: #54b965;
    --name-green: #25a444;
    --paper: #ffffff;
    --ink: #222426;
    --icon-blue: #3b6da6;
  }
  * { margin: 0; padding: 0; box-sizing: border-box; }
  html, body {
    width: 900px; height: 1200px; overflow: hidden;
    background: var(--backdrop);
  }
  .canvas { position: relative; width: 900px; height: 1200px; }

  .card { position: absolute; left: 117px; width: 665px; height: 379px; }

  .card--front {
    top: 201px;
    background: radial-gradient(ellipse at 50% 85%, var(--brand-green-light), var(--brand-green) 75%);
    color: var(--paper);
    text-align: center;
  }
  .brand-name {
    position: absolute; left: 0; right: 0; top: 140px;
    font-family: "Comfortaa", sans-serif;
    font-weight: 700;
    font-size: 44px;
    letter-spacing: -0.5px;
  }
  .tagline {
    position: absolute; left: 0; right: 0; top: 215px;
    font-family: "Comfortaa", sans-serif;
    font-weight: 300;
    font-size: 16px;
    letter-spacing: 0.6px;
  }

  .card--back { top: 617px; background: var(--paper); }
  .person-name {
    position: absolute; right: 350px; top: 174px;
    font-family: "Comfortaa", sans-serif;
    font-weight: 700;
    font-size: 25px;
    color: var(--name-green);
    white-space: nowrap;
  }
  .contact-list {
    position: absolute; left: 326px; top: 154px;
    list-style: none;
    font-family: "Open Sans", sans-serif;
    font-size: 15px;
    color: var(--ink);
  }
  .contact-item { display: flex; align-items: center; height: 23.5px; letter-spacing: 0.5px; }
  .contact-item--phone { letter-spacing: 2.4px; }
  .contact-icon { width: 13px; height: 13px; margin-right: 12px; fill: var(--icon-blue); flex: none; }
</style>
</head>
<body>
<main class="canvas">
  <section class="card card--front">
    <h1 class="brand-name">tolvikcleaning.com</h1>
    <p class="tagline">better because we care</p>
  </section>

  <section class="card card--back">
    <h2 class="person-name">maren cole</h2>
    <ul class="contact-list">
      <li class="contact-item contact-item--phone">
        <svg class="contact-icon" viewBox="0 0 16 16" aria-hidden="true"><path d="M3.6 1.2l2.2 2.6c.3.4.3.9 0 1.3L4.7 6.3c.8 1.9 2.6 3.8 4.9 5l1.2-1.1c.4-.3.9-.3 1.3 0l2.6 2.2c.4.3.4.9.1 1.3l-1.2 1.3c-.5.5-1.3.7-2 .4C6.3 13.5 2.5 9.7.8 4.4.6 3.7.8 2.9 1.3 2.4L2.4 1.2c.3-.4.9-.4 1.2 0z"/></svg>
        (555) 014-2738
      </li>
      <li class="contact-item">
        <svg class="contact-icon" viewBox="0 0 16 16" aria-hidden="true"><path d="M1 3h14v1.6L8 9 1 4.6z"/><path d="M1 6.4l7 4.4 7-4.4V13H1z"/></svg>
        maren@tolvikcleaning.com
      </li>
      <li class="contact-item">
        <svg class="contact-icon" viewBox="0 0 16 16" aria-hidden="true"><circle cx="8" cy="8" r="7.2"/><path d="M5 3.5c1.5.5 2 1.6 1.2 2.6-.7.8.4 1.6 1.6 1.4 1.3-.2 1.2 1.6.2 2.4-.8.7-.4 2 .3 2.8" fill="none" stroke="#fff" stroke-width="1.3"/></svg>
        www.tolvikcleaning.com
      </li>
    </ul>
  </section>
</main>
</body>
</html>
```